TA BRAMLEY BUSINESS CARD DESIGN PROJECT

We need to utilize our logo that was expertly created on PixelHarbor and now need to match this with a business card design.

```html
<!DOCTYPE html>
<html lang="en">
<head>
<meta charset="UTF-8">
<title>TA Bramley Business Card</title>
<link rel="stylesheet" href="https://fonts.googleapis.com/css2?family=Montserrat:wght@400;500;700&family=Roboto:wght@700;900&display=swap">
<style>
  :root {
    --brand-blue: #1057aa;
    --paper: #ffffff;
    --ink: #2b2b2b;
    --backdrop: #e4e4e4;
  }
  * { margin: 0; padding: 0; box-sizing: border-box; }
  html, body { width: 1200px; height: 800px; overflow: hidden; }
  body {
    background: var(--backdrop);
    font-family: "Montserrat", Arial, sans-serif;
    position: relative;
  }
  .card {
    position: absolute;
    border-radius: 28px;
    box-shadow: 0 6px 18px rgba(0,0,0,0.18);
  }
  .card-front {
    left: 170px; top: 120px;
    width: 330px; height: 560px;
    background: var(--paper);
    border-bottom: 4px solid var(--brand-blue);
    display: flex; flex-direction: column; align-items: center;
    padding-top: 70px;
  }
  .card-back {
    left: 560px; top: 235px;
    width: 560px; height: 330px;
    background: var(--brand-blue);
    display: flex; align-items: center; justify-content: center;
  }
  .brand-name {
    font-family: "Montserrat", Arial, sans-serif;
    font-weight: 700;
    color: var(--brand-blue);
    font-size: 34px;
    letter-spacing: 4px;
  }
  .card-back .brand-name {
    color: var(--paper);
    font-size: 62px;
    letter-spacing: 10px;
  }
  .person-name {
    margin-top: 36px;
    font-family: "Roboto", Arial, sans-serif;
    font-weight: 900;
    color: var(--brand-blue);
    font-size: 21px;
    letter-spacing: 0.5px;
  }
  .person-title {
    margin-top: 2px;
    font-size: 14px;
    color: var(--ink);
    letter-spacing: 0.5px;
  }
  .dot-row { display: block; margin-top: 150px; }
  .dot-row.address-row { margin-top: 10px; }
  .contact-list {
    list-style: none;
    text-align: center;
    font-size: 15px;
    color: var(--ink);
    line-height: 21px;
    margin-top: 8px;
  }
  .address {
    text-align: center;
    font-size: 15px;
    color: var(--ink);
    line-height: 21px;
    margin-top: 8px;
    font-style: normal;
  }
</style>
</head>
<body>

<section class="card card-front">
  <div class="brand-name">TA BRAMLEY</div>
  <div class="person-name">DANA WHITLOCK</div>
  <div class="person-title">Managing Director</div>

  <svg class="dot-row contact-row" width="290" height="30" viewBox="0 0 290 30" aria-hidden="true">
    <g fill="#1057aa">
      <circle cx="8" cy="15" r="2"/><circle cx="22" cy="15" r="3"/><circle cx="38" cy="15" r="4"/>
      <circle cx="56" cy="15" r="5"/><circle cx="76" cy="15" r="6"/>
      <circle cx="106" cy="15" r="14"/><circle cx="145" cy="15" r="14"/><circle cx="184" cy="15" r="14"/>
      <circle cx="214" cy="15" r="6"/><circle cx="234" cy="15" r="5"/><circle cx="252" cy="15" r="4"/>
      <circle cx="268" cy="15" r="3"/><circle cx="282" cy="15" r="2"/>
    </g>
    <path class="icon-phone" d="M101 9 l3 -1 l2 4 l-2 1.5 q1 3 4 4.5 l1.5 -2 l4 2 l-1 3 q-8 0 -11.5 -12z" fill="#fff"/>
    <g class="icon-mail" fill="none" stroke="#fff" stroke-width="1.6">
      <rect x="138" y="10" width="14" height="10" rx="1" fill="#fff" stroke="none"/>
      <polyline points="138,10 145,16 152,10" stroke="#1057aa"/>
    </g>
    <g class="icon-globe" fill="none" stroke="#fff" stroke-width="1.4">
      <circle cx="184" cy="15" r="7"/>
      <ellipse cx="184" cy="15" rx="3" ry="7"/>
      <line x1="177" y1="15" x2="191" y2="15"/>
    </g>
  </svg>

  <ul class="contact-list">
    <li>123 456 789</li>
    <li>info@tabramley.com</li>
    <li>www.tabramley.com</li>
  </ul>

  <svg class="dot-row address-row" width="290" height="30" viewBox="0 0 290 30" aria-hidden="true">
    <g fill="#1057aa">
      <circle cx="8" cy="15" r="2"/><circle cx="22" cy="15" r="3"/><circle cx="38" cy="15" r="4"/>
      <circle cx="56" cy="15" r="5"/><circle cx="76" cy="15" r="6"/><circle cx="102" cy="15" r="7"/>
      <circle cx="145" cy="15" r="14"/>
      <circle cx="188" cy="15" r="7"/><circle cx="214" cy="15" r="6"/><circle cx="234" cy="15" r="5"/>
      <circle cx="252" cy="15" r="4"/><circle cx="268" cy="15" r="3"/><circle cx="282" cy="15" r="2"/>
    </g>
    <path class="icon-pin" d="M145 23 q-6 -7 -6 -11 a6 6 0 0 1 12 0 q0 4 -6 11z" fill="#fff"/>
    <circle cx="145" cy="12" r="2.2" fill="#1057aa"/>
  </svg>

  <address class="address">Your address, City<br>State, Zip 1234</address>
</section>

<section class="card card-back">
  <div class="brand-name">TA BRAMLEY</div>
</section>

</body>
</html>
```